Business Card Design for Property Development Company Director

I am looking for a professional and unforgettable business card design for our Director of our Property Development Company.
Please see attached .pptx file to find out what information to include. You don't have to follow the exact format shown in the file - I am interested to see your creative flair using the information provided.

```html
<!DOCTYPE html>
<html lang="en">
<head>
<meta charset="utf-8">
<title>Halvern Property Group – Business Card</title>
<link rel="stylesheet" href="https://fonts.googleapis.com/css2?family=Roboto:wght@400;500;700&family=Roboto+Condensed:wght@700&display=swap">
<style>
  :root {
    --bg: #e4e5e7;
    --card: #f7f7f7;
    --blue: #23479a;
    --grey: #55585d;
    --grey-light: #6b6e73;
  }
  * { box-sizing: border-box; margin: 0; padding: 0; }
  html, body { width: 1200px; height: 726px; overflow: hidden; }
  body {
    background: var(--bg);
    font-family: "Roboto", sans-serif;
    position: relative;
  }
  .card {
    position: absolute;
    width: 540px;
    height: 309px;
    background: var(--card);
    box-shadow: 0 6px 18px rgba(0,0,0,0.12);
    overflow: hidden;
  }
  .card-front { left: 40px; top: 208px; }
  .card-back { left: 620px; top: 208px; }

  /* front */
  .tagline {
    position: absolute; top: 34px; left: 0; right: 0;
    text-align: center; color: var(--blue);
    font-size: 17px; line-height: 21px; font-weight: 400;
  }
  .wordmark {
    display: flex; align-items: center; gap: 12px;
    color: var(--blue); font-weight: 700;
  }
  .wordmark-square { background: var(--blue); flex: none; }
  .wordmark-text { display: flex; flex-direction: column; line-height: 1; }
  .front-wordmark { position: absolute; top: 100px; left: 0; right: 0; justify-content: center; }
  .front-wordmark .wordmark-square { width: 46px; height: 46px; }
  .front-wordmark .name { font-size: 50px; letter-spacing: 1px; }
  .front-wordmark .sub { font-size: 15px; letter-spacing: 5.6px; margin-top: 4px; }
  .pitch {
    position: absolute; top: 210px; left: 0; right: 0;
    text-align: center; color: var(--grey-light); font-size: 14px;
  }
  .pitch .highlight { color: var(--blue); }
  .band {
    position: absolute; left: 0; right: 0; height: 12px; display: flex;
  }
  .band-grey { background: var(--grey); }
  .band-blue { background: var(--blue); flex: 1; }
  .card-front .band { top: 262px; }
  .card-front .band-grey { width: 56%; }

  /* back */
  .person { position: absolute; left: 32px; top: 70px; }
  .person-name {
    font-family: "Roboto Condensed", sans-serif; font-weight: 700;
    color: var(--blue); font-size: 23px;
  }
  .person-role { color: var(--grey-light); font-size: 12.5px; margin-top: 2px; }
  .contacts {
    position: absolute; left: 62px; top: 150px;
    list-style: none; color: var(--grey); font-size: 14px; line-height: 19px;
  }
  .contacts li { display: flex; align-items: center; gap: 10px; }
  .contacts svg { width: 12px; height: 12px; flex: none; }
  .licence { margin-top: 2px; }
  .licence-number { color: var(--blue); }
  .card-back .band { top: 278px; height: 10px; }
  .card-back .band-grey { width: 63%; }
  .back-wordmark {
    position: absolute; right: 22px; top: 30px;
    writing-mode: vertical-rl; transform: rotate(180deg);
    gap: 10px;
  }
  .back-wordmark .wordmark-text { flex-direction: column; gap: 3px; }
  .back-wordmark .wordmark-square { width: 32px; height: 32px; }
  .back-wordmark .name { font-size: 32px; letter-spacing: 1px; }
  .back-wordmark .sub { font-size: 10px; letter-spacing: 3.4px; font-weight: 500; }
</style>
</head>
<body>
  <section class="card card-front" aria-label="Card front">
    <p class="tagline">Property Development<br>&amp; Site Acquisition Specialists</p>
    <div class="wordmark front-wordmark">
      <span class="wordmark-square"></span>
      <span class="wordmark-text">
        <span class="name">HALVERN</span>
        <span class="sub">PROPERTY GROUP</span>
      </span>
    </div>
    <p class="pitch">Ask me about our <span class="highlight">INVESTMENT &amp; PARTNERSHIP</span> opportunities</p>
    <div class="band"><span class="band-grey"></span><span class="band-blue"></span></div>
  </section>

  <section class="card card-back" aria-label="Card back">
    <div class="person">
      <p class="person-name">Daniel Marsh</p>
      <p class="person-role">Director</p>
    </div>
    <ul class="contacts">
      <li>
        <svg viewBox="0 0 12 12" aria-hidden="true"><path d="M2.5 1 L4.5 1 L5 3.5 L3.8 4.4 Q4.8 6.8 7.6 8.2 L8.5 7 L11 7.5 L11 9.5 Q10.5 11 9 11 Q2 10 1 3 Q1 1.5 2.5 1Z" fill="var(--blue)"/></svg>
        0400 123 456
      </li>
      <li>
        <svg viewBox="0 0 12 12" aria-hidden="true"><rect x="0.5" y="2.5" width="11" height="7.5" fill="var(--blue)"/><path d="M0.8 2.8 L6 7 L11.2 2.8" stroke="#fff" stroke-width="1" fill="none"/></svg>
        daniel@halvern.com.au
      </li>
      <li>
        <svg viewBox="0 0 12 12" aria-hidden="true"><circle cx="6" cy="6" r="5.3" fill="var(--blue)"/><path d="M0.7 6 H11.3 M6 0.7 V11.3 M6 0.7 Q2.5 6 6 11.3 M6 0.7 Q9.5 6 6 11.3" stroke="#fff" stroke-width="0.7" fill="none"/></svg>
        www.halvern.com.au
      </li>
      <li class="licence">Real Estate Lic:</li>
      <li class="licence-number">1234567 &amp; 1234568</li>
    </ul>
    <div class="band"><span class="band-grey"></span><span class="band-blue"></span></div>
    <div class="wordmark back-wordmark">
      <span class="wordmark-square"></span>
      <span class="wordmark-text">
        <span class="name">HALVERN</span>
        <span class="sub">PROPERTY GROUP</span>
      </span>
    </div>
  </section>
</body>
</html>
```